Business Card Design for Varomir Facility Services

We are looking for a Business Card Design for the Company "Varomir Facility Services."
Front side:
- Company Logo (small)
- Company Name, address, pohone, website and personal data.
- white background, for text e.g. company colors (blue or green like in the logo)
Please use following data:
Company data:
Varomir Facility Services Kostelac
Birkenhaldweg 14
6330 Cham
www.varomir-fs.ch
Person data:
Tarik Kostelac
Geschäftsführer
+41 76 519 47 83
info@varomir-fs.ch
Back side:
could be colored in blue or green
please use a big logo sing and some smaller icons to say what is all beeing offered in facility services, like cleaning, maintenance cleaning
industrial cleaning, caretaking, gardening, disposal. There is no need for everyone of the icons if there are similar or an icon is standing for more of them.
colors to use:
blue: HEX 246BB0
green: HEX 52B33E

```html
<!DOCTYPE html>
<html lang="de">
<head>
<meta charset="utf-8">
<title>Varomir Facility Services – Visitenkarte</title>
<link rel="stylesheet" href="https://fonts.googleapis.com/css2?family=Montserrat:wght@500;600;700&family=Open+Sans:wght@400&display=swap">
<style>
  :root {
    --brand-blue: #246BB0;
    --brand-green: #52B33E;
    --panel-green: #1FAE4B;
    --paper: #FFFFFF;
    --backdrop: #2A2B2D;
    --ink-light: #FFFFFF;
  }
  * { box-sizing: border-box; margin: 0; padding: 0; }
  html, body {
    width: 1200px; height: 900px; overflow: hidden;
    background: var(--backdrop);
  }
  .sheet {
    position: relative; width: 1200px; height: 900px;
  }
  .card {
    position: absolute; left: 280px; width: 640px; height: 380px;
    overflow: hidden; box-shadow: 0 12px 30px rgba(0,0,0,0.45);
  }

  /* Back side */
  .card--back { top: 50px; background: var(--brand-blue); }
  .wordmark {
    position: absolute; display: flex; align-items: center; gap: 14px;
  }
  .wordmark__dot {
    width: 34px; height: 34px; border-radius: 50%;
    background: var(--brand-green); flex: none;
  }
  .wordmark__name {
    font-family: "Montserrat", sans-serif; font-weight: 600;
    letter-spacing: 0.04em; text-transform: uppercase; line-height: 1.15;
  }
  .card--back .wordmark { left: 150px; top: 92px; }
  .card--back .wordmark__name { color: var(--ink-light); font-size: 28px; }

  .services {
    position: absolute; left: 30px; right: 30px; top: 250px;
    display: flex; justify-content: space-between; list-style: none;
  }
  .service {
    display: flex; flex-direction: column; align-items: center; gap: 10px;
    font-family: "Open Sans", sans-serif; font-size: 15px; color: var(--ink-light);
    white-space: nowrap;
  }
  .service__icon {
    width: 40px; height: 40px; border-radius: 50%;
    background: radial-gradient(circle at 40% 35%, #6CC757, var(--brand-green));
  }

  /* Front side */
  .card--front { top: 470px; background: var(--paper); }
  .card--front .wordmark { left: 28px; top: 160px; }
  .card--front .wordmark__dot { width: 26px; height: 26px; }
  .card--front .wordmark__name { color: var(--brand-blue); font-size: 19px; }

  .panel {
    position: absolute; left: 330px; right: 0;
    padding: 30px 26px 0 34px; color: var(--ink-light);
    font-family: "Montserrat", sans-serif;
  }
  .panel--person { top: 0; height: 180px; background: var(--brand-blue); }
  .panel--company { top: 180px; height: 200px; background: var(--panel-green); padding-top: 28px; }

  .panel__title {
    font-weight: 700; font-size: 17px; text-transform: uppercase;
    letter-spacing: 0.02em; line-height: 1.2;
  }
  .panel__role { font-weight: 500; font-size: 15px; margin: 4px 0 12px; }
  .panel__line {
    display: flex; align-items: center; gap: 9px;
    font-weight: 500; font-size: 15px; line-height: 1.6;
  }
  .panel__line svg { width: 13px; height: 13px; flex: none; }
  .panel__address { font-weight: 500; font-size: 15px; line-height: 1.35; margin: 8px 0 12px; }
</style>
</head>
<body>
<main class="sheet">

  <section class="card card--back" aria-label="Rückseite">
    <div class="wordmark">
      <span class="wordmark__dot"></span>
      <span class="wordmark__name">Varomir<br>Facility Services</span>
    </div>
    <ul class="services">
      <li class="service"><span class="service__icon" role="img" aria-label="Icon: Unterhaltsreinigung"></span>Maintenance cleaning</li>
      <li class="service"><span class="service__icon" role="img" aria-label="Icon: Industriereinigung"></span>Industrial cleaning</li>
      <li class="service"><span class="service__icon" role="img" aria-label="Icon: Hauswartung"></span>Caretaking</li>
      <li class="service"><span class="service__icon" role="img" aria-label="Icon: Gartenpflege"></span>Gardening</li>
      <li class="service"><span class="service__icon" role="img" aria-label="Icon: Entsorgung"></span>Disposal</li>
    </ul>
  </section>

  <section class="card card--front" aria-label="Vorderseite">
    <div class="wordmark">
      <span class="wordmark__dot"></span>
      <span class="wordmark__name">Varomir<br>Facility Services</span>
    </div>

    <div class="panel panel--person">
      <p class="panel__title">Tarik Kostelac</p>
      <p class="panel__role">Geschäftsführer</p>
      <p class="panel__line">
        <svg viewBox="0 0 16 16" aria-hidden="true"><path fill="#fff" d="M3.6 1.2l2.3 2.6-1.3 1.8c.9 2 2.5 3.6 4.6 4.6l1.8-1.3 2.6 2.3-1.5 2.3C6.9 13.9 2.1 9.1 1.3 2.7z"/></svg>
        +41 76 519 47 83
      </p>
      <p class="panel__line">
        <svg viewBox="0 0 16 16" aria-hidden="true"><rect x="1" y="3" width="14" height="10" fill="none" stroke="#fff" stroke-width="1.6"/><path d="M1.5 3.5L8 9l6.5-5.5" fill="none" stroke="#fff" stroke-width="1.6"/></svg>
        info@varomir-fs.ch
      </p>
    </div>

    <div class="panel panel--company">
      <p class="panel__title">Varomir Facility<br>Services Kostelac</p>
      <p class="panel__address">Birkenhaldweg 14<br>6330 Cham</p>
      <p class="panel__line">
        <svg viewBox="0 0 16 16" aria-hidden="true"><circle cx="8" cy="8" r="6.5" fill="none" stroke="#fff" stroke-width="1.5"/><ellipse cx="8" cy="8" rx="2.8" ry="6.5" fill="none" stroke="#fff" stroke-width="1.2"/><path d="M1.5 8h13" stroke="#fff" stroke-width="1.2"/></svg>
        www.varomir-fs.ch
      </p>
    </div>
  </section>

</main>
</body>
</html>
```